TLV Accounting Firm Needs Graphic Art for Our Proven Processes and For Our Core Values

**Looking for redesign of attached Powerpoint content (see below)
***Final graphic should be good for web use

Date: March 10, 2017

From: Colin Ashdown, CPA
Ashdown, Pettifer & Associates, P.C. (TLV)

Background:

TLV is a 20 person Houston based CPA firm, providing tax, accounting, financial and consulting services, to individuals and to entrepreneurs and their businesses. TLV is engaged in a process called KLU (See the book Headway, by Lars Obermeyer) whereby we implement a “system” to operate our company. As part of this system we have defined what we call our “Proven Process”. This is something we will show all prospective clients, and have on our website, that explains what it looks like to work with us. Starting at the beginning of the project to completion.

Project Description:

TLV is looking for graphic artist assistance in designing the following pieces:

1. Graphic depiction of “The TLV Way”, otherwise known as our “Proven Process”. The first attachments labeled TLV will show what we have done ourselves. These will show the general steps we have defined in both a sort of graphic way and a step by step narrative. The second attachment shows you some actual examples other firms have put together, hopefully that will show you what we are asking you to develop for us. Note that we are very open to any suggested clarifications or improvements to what we have done which may include changing phrases or saying something in a different way. Remember we are accountants!

2. We have defined our core values as a company, and we are wanting to develop some posters/placards so we can post them in our conference rooms, break room, etc. Attached are our core values as well as some deeper narratives about what they mean. Also included are many of the “words” we kicked around before arriving at our core values.

3. You will also find an attachment with our logo that should be incorporated, as well. Designs SHOULD INCLUDE, but not be limited to, the colors on our logo. Our end product should reflect a strong sense of our core values.

We would like to have the project in a form that would give us the option to use any/all of the information on our website, posters, brochures, etc.

Thanks in advance for your assistance.

Target Market(s)

Entrepreneurs and their companies with revenue greater than one million; Industries such as real estate, construction, trades and professional services; all in the Greater Houston Texas area

Industry/Entity Type

Accounting

Font styles to use
Serif
Other font styles liked:
• We are okay with Serif but are open.

Requirements
Must have
• Proven Process must be presented in a way that is clear and makes sense.
Nice to have
• Clean lines
• Colors should go with logo (see attached)
Should not have
• Can't think of anything - unless I see it

```html
<!DOCTYPE html>
<html lang="en">
<head>
<meta charset="utf-8">
<title>Client Service Approach – Ashdown, Pettifer &amp; Associates, PC</title>
<link rel="stylesheet" href="https://fonts.googleapis.com/css2?family=Fira+Sans:wght@500;700;800&display=swap">
<style>
  :root {
    --ink-title: #58595b;
    --ink-label: #3f3f41;
    --ink-brand: #3d3a1f;
    --brand-accent: #b89a3e;
    --rule: #6d6e71;
    --page: #ffffff;
    --footer-end: #dedddf;
    --footer-edge: #c9c9cb;
  }
  * { margin: 0; padding: 0; box-sizing: border-box; }
  html, body { width: 1200px; height: 675px; overflow: hidden; background: var(--page); }
  .slide {
    position: relative;
    width: 1200px;
    height: 675px;
    overflow: hidden;
    background: var(--page);
    font-family: "Fira Sans", Arial, sans-serif;
  }
  .slide-title {
    position: absolute;
    left: 29px;
    top: 30px;
    font-size: 45px;
    font-weight: 800;
    letter-spacing: 0.2px;
    color: var(--ink-title);
    line-height: 1;
  }
  .approach-diagram {
    position: absolute;
    left: 0;
    top: 0;
    width: 1200px;
    height: 564px;
  }
  .approach-label {
    position: absolute;
    left: 719px;
    font-size: 22px;
    font-weight: 700;
    color: var(--ink-label);
    line-height: 1;
    white-space: nowrap;
  }
  .label-peace { top: 184px; }
  .label-focus { top: 285px; }
  .label-caring { top: 390px; }
  .label-long-term { top: 458px; }
  .footer-band {
    position: absolute;
    left: 0;
    top: 564px;
    width: 1200px;
    height: 111px;
    background: linear-gradient(90deg, var(--page) 0%, var(--page) 35%, var(--footer-end) 100%);
    border-top: 2px solid var(--footer-edge);
    box-shadow: inset 0 6px 8px -6px rgba(0,0,0,0.18);
  }
  .firm-name {
    position: absolute;
    left: 30px;
    top: 42px;
    display: flex;
    align-items: center;
    gap: 10px;
    font-size: 19px;
    font-weight: 500;
    color: var(--ink-brand);
    white-space: nowrap;
  }
  .firm-mark {
    width: 14px;
    height: 14px;
    background: var(--brand-accent);
  }
</style>
</head>
<body>
<main class="slide">
  <h1 class="slide-title">CLIENT SERVICE APPROACH</h1>

  <svg class="approach-diagram" viewBox="0 0 1200 564" aria-hidden="true">
    <defs>
      <linearGradient id="ring-blue" x1="0" y1="0" x2="0" y2="1">
        <stop offset="0" stop-color="#29abe2"/>
        <stop offset="0.6" stop-color="#27a4dd"/>
        <stop offset="1" stop-color="#1b75bc"/>
      </linearGradient>
      <linearGradient id="ring-yellow" x1="0" y1="0" x2="0" y2="1">
        <stop offset="0" stop-color="#f8ec31"/>
        <stop offset="0.55" stop-color="#f9e532"/>
        <stop offset="1" stop-color="#f7941d"/>
      </linearGradient>
      <linearGradient id="ring-green" x1="0" y1="0" x2="0" y2="1">
        <stop offset="0" stop-color="#8dc63f"/>
        <stop offset="0.55" stop-color="#7cbf40"/>
        <stop offset="1" stop-color="#0f9a48"/>
      </linearGradient>
      <linearGradient id="ring-pink" x1="0" y1="0" x2="0" y2="1">
        <stop offset="0" stop-color="#ec297b"/>
        <stop offset="0.55" stop-color="#e2287a"/>
        <stop offset="1" stop-color="#9e1f63"/>
      </linearGradient>
    </defs>

    <circle cx="419" cy="337" r="199" fill="url(#ring-blue)"/>
    <circle cx="419" cy="386" r="150" fill="url(#ring-yellow)"/>
    <circle cx="419" cy="436" r="100" fill="url(#ring-green)"/>
    <circle cx="419" cy="485" r="51" fill="url(#ring-pink)"/>

    <g stroke="var(--rule)" stroke-width="1">
      <line x1="419" y1="212" x2="878" y2="212"/>
      <line x1="419" y1="313" x2="878" y2="313"/>
      <line x1="419" y1="418" x2="868" y2="418"/>
      <line x1="419" y1="485" x2="995" y2="485"/>
    </g>
    <g fill="#ffffff" stroke="var(--rule)" stroke-width="1">
      <circle cx="419" cy="212" r="4.5"/>
      <circle cx="419" cy="313" r="4.5"/>
      <circle cx="419" cy="418" r="4.5"/>
      <circle cx="419" cy="485" r="4.5"/>
    </g>
  </svg>

  <p class="approach-label label-peace">Peace of mind</p>
  <p class="approach-label label-focus">Client focus</p>
  <p class="approach-label label-caring">Caring touch</p>
  <p class="approach-label label-long-term">Long term relationships</p>

  <footer class="footer-band">
    <div class="firm-name"><span class="firm-mark"></span>Ashdown, Pettifer &amp; Associates, PC</div>
  </footer>
</main>
</body>
</html>
```